New Business Card for Software Company

We are looking at rebranding a 10 year old company that specializes in PDF and DWF solutions for Architects and Engineers. We will attach the new company logo that we are going with so you can work with that and complimentary colors.
The sample information we would like on the business card is:
Gerald Pinfold
Vice President
4738 W. Harrowgate Lane. STE 305
PMB#417
Corvell, NM 85374
866-392-5074 US Toll Free
123-456-3190 Cell
gpinfold@plavorix.com
The old tag line that we had on the business cars was.
Delivering Dependable Drawing File Tools to Design Teams Around the World.
If you have an idea for a better tag line we are open to that also.
Updates
We would like to thank all of the Designers for their wonderful work. We apologize that we will not have the time to provide feedback to everyone. There is just so many innovative and professional designs that you have all created making our decision even harder.
Target Market(s)
Architects and Engineers
Industry/Entity Type
Business
Look and feel

```html
<!DOCTYPE html>
<html lang="en">
<head>
<meta charset="utf-8">
<title>Plavorix Business Card</title>
<link rel="stylesheet" href="https://fonts.googleapis.com/css2?family=Arimo:wght@400;700&family=PT+Sans&display=swap">
<style>
  :root {
    --orange: #e8581c;
    --orange-light: #f4912a;
    --grey: #5b5b5b;
    --text: #3d3d3d;
    --card: #ffffff;
    --backdrop: #e9e6e1;
    --edge: #d6d2cc;
  }
  * { margin: 0; padding: 0; box-sizing: border-box; }
  html, body { width: 1200px; height: 720px; overflow: hidden; }
  body {
    background: var(--backdrop);
    font-family: "Arimo", Arial, sans-serif;
    color: var(--text);
  }
  .canvas {
    width: 1200px; height: 720px;
    display: flex; align-items: center; justify-content: center; gap: 40px;
  }
  .card {
    position: relative;
    width: 540px; height: 309px;
    background: var(--card);
    border: 1px solid var(--edge);
    box-shadow: 0 6px 18px rgba(0,0,0,0.12);
  }

  /* Front side */
  .card-front .wordmark {
    position: absolute; left: 32px; top: 46px;
    font-size: 42px; font-weight: 700; letter-spacing: -1px;
    color: var(--orange);
  }
  .card-front .mark-circle {
    position: absolute; right: 40px; top: 26px;
    width: 150px; height: 150px; border-radius: 50%;
    background: var(--orange-light);
  }
  .person { position: absolute; left: 34px; top: 104px; }
  .person-name { font-size: 21px; font-weight: 700; color: var(--orange); }
  .person-title { font-size: 13px; color: var(--grey); margin-top: 1px; }
  .contact-list { position: absolute; left: 34px; top: 156px; list-style: none; }
  .contact-list li {
    display: flex; align-items: center; gap: 8px;
    font-size: 13px; color: var(--grey); line-height: 22px;
  }
  .contact-list svg { width: 12px; height: 12px; fill: var(--orange); flex: none; }
  .address {
    position: absolute; left: 34px; top: 234px;
    font-size: 13px; line-height: 17px; color: var(--grey); font-style: normal;
  }

  /* Back side */
  .card-back .logo-lockup {
    position: absolute; left: 70px; top: 92px;
    display: flex; align-items: center; gap: 18px;
  }
  .card-back .mark-circle {
    width: 96px; height: 96px; border-radius: 50%;
    background: var(--orange-light);
  }
  .card-back .wordmark {
    font-size: 60px; font-weight: 700; letter-spacing: -2px; color: var(--orange);
  }
  .tagline {
    position: absolute; left: 0; right: 0; top: 218px;
    text-align: center;
    font-family: "PT Sans", "Myriad Pro", sans-serif;
    font-size: 16px; line-height: 21px; color: var(--grey);
  }
</style>
</head>
<body>
<main class="canvas">
  <section class="card card-front" aria-label="Business card front">
    <div class="wordmark">Plavorix</div>
    <div class="mark-circle" aria-hidden="true"></div>
    <div class="person">
      <div class="person-name">Gerald Pinfold</div>
      <div class="person-title">Vice President</div>
    </div>
    <ul class="contact-list">
      <li>
        <svg viewBox="0 0 24 24" aria-hidden="true"><path d="M6.6 10.8a15.1 15.1 0 0 0 6.6 6.6l2.2-2.2c.3-.3.7-.4 1-.2 1.1.4 2.300.6 3.600.6.6 0 1 .4 1 1V20c0 .6-.4 1-1 1C10.600 21 3 13.400 3 4c0-.6.4-1 1-1h3.500c.6 0 1 .4 1 1 0 1.300.2 2.500.6 3.600.1.3 0 .7-.2 1z"/></svg>
        866-392-5074(US) TF
      </li>
      <li>
        <svg viewBox="0 0 24 24" aria-hidden="true"><path d="M7 1h10a2 2 0 0 1 2 2v18a2 2 0 0 1-2 2H7a2 2 0 0 1-2-2V3a2 2 0 0 1 2-2zm0 3v14h10V4zm5 15.5a1.2 1.2 0 1 0 0 2.4 1.2 1.2 0 0 0 0-2.4z"/></svg>
        123-456-3190
      </li>
      <li>
        <svg viewBox="0 0 24 24" aria-hidden="true"><path d="M2 5h20v14H2zm2 2v.5l8 5 8-5V7zm0 2.8V17h16V9.8l-8 5z"/></svg>
        gpinfold@plavorix.com
      </li>
    </ul>
    <address class="address">
      4738 W. Harrowgate Lane<br>
      STE 305<br>
      PMB#417, Corvell, NM 85374
    </address>
  </section>

  <section class="card card-back" aria-label="Business card back">
    <div class="logo-lockup">
      <div class="mark-circle" aria-hidden="true"></div>
      <div class="wordmark">Plavorix</div>
    </div>
    <p class="tagline">Delivering Dependable Drawing File Tools<br>to Design Teams Around the World</p>
  </section>
</main>
</body>
</html>
```